New Wix logo and website layout

I need a new logo design and a new, modern website layout design. I am a professional therapist providing remedial massage. I am Canadian but live in Australia & would like the logo to have a somewhat 'Canadian feel' to it (something subtle i.e. no flags) I currently have a maple tree leaf as my logo. my current website is cedarlinemassage.com.au. I need the website to work on mobile phones & traditional web browsers.

Target Market(s)

customers looking for remedial massage and manual lymphatic drainage

Industry/Entity Type

professional massage

Coding

Coded - Design and coding required

Font styles to use
Sans Serif

Colors
EB3D1F
EC4F4E
F09395
F8D3D4
FCEDEE

Requirements
Nice to have
• something subtle that indicates that I am canadian
Should not have
• no flags. nothing too bold

```html
<!DOCTYPE html>
<html lang="en">
<head>
<meta charset="utf-8">
<title>Cedarline Massage</title>
<link rel="stylesheet" href="https://fonts.googleapis.com/css2?family=Poppins:wght@400;500;600;700&display=swap">
<style>
:root{
  --red:#EB3D1F;
  --coral:#EC4F4E;
  --pink:#F09395;
  --blush:#F8D3D4;
  --mist:#FCEDEE;
  --ink:#2b2b2b;
  --text:#444;
  --black:#0a0a0a;
  --white:#fff;
}
*{box-sizing:border-box;margin:0;padding:0}
html,body{width:1200px;height:3629px;overflow:hidden;background:var(--white)}
body{position:relative;font-family:Arial,Helvetica,sans-serif;color:var(--text)}
.abs{position:absolute}
.heading{font-family:'Poppins',sans-serif;font-weight:500;color:var(--ink)}
.rule{position:absolute;height:3px;width:50px;background:var(--red)}
.btn{position:absolute;background:var(--red);color:var(--white);border-radius:30px;font-family:'Poppins',sans-serif;font-weight:500;display:flex;align-items:center;justify-content:center;white-space:nowrap}

/* hero */
.hero-photo{position:absolute;left:0;top:0;width:1200px;height:845px;background:radial-gradient(ellipse at 70% 55%,#b9a58e 0%,#c98a3a 35%,#e29a1c 60%,#b85a0c 100%)}
.waves{position:absolute;left:0;top:0;width:1200px;height:3629px;pointer-events:none;z-index:1}
.logo-tab{position:absolute;left:113px;top:0;width:141px;height:180px;background:var(--white);border-radius:0 0 70px 70px;display:flex;flex-direction:column;align-items:center;justify-content:flex-end;padding-bottom:26px}
.logo-dot{width:52px;height:52px;border-radius:50%;border:3px solid var(--red);margin-bottom:10px}
.logo-name{font-family:'Poppins',sans-serif;font-weight:600;font-size:13px;color:var(--ink);text-align:center;line-height:1.25;white-space:nowrap}
.topbar{position:absolute;top:22px;left:305px;font-family:'Poppins',sans-serif;font-size:14px;color:var(--white);display:flex;gap:28px;align-items:center;white-space:nowrap}
.topbar span{display:flex;align-items:center;gap:10px}
.nav{position:absolute;left:254px;top:68px;width:760px;height:67px;background:var(--white);border-radius:0 34px 34px 0;display:flex;align-items:center;font-family:'Poppins',sans-serif;font-size:15px;color:var(--ink)}
.nav a{position:absolute;color:inherit;text-decoration:none;white-space:nowrap}
.login{left:636px;top:10px;width:113px;height:47px;font-size:16px}
.hero-title{left:592px;top:430px;font-family:'Poppins',sans-serif;font-weight:600;font-size:45px;color:var(--white);letter-spacing:-.5px;white-space:nowrap}
.hero-sub{left:592px;top:502px;font-family:'Poppins',sans-serif;font-weight:600;font-size:18px;line-height:35px;color:var(--white);white-space:nowrap}
.dots{left:916px;top:809px;display:flex;gap:8px;z-index:2}
.dots i{width:11px;height:11px;border-radius:50%;background:var(--white)}
.dots i.on{background:var(--red)}

/* services */
.section-title{position:absolute;left:0;width:1200px;text-align:center;font-size:37px}
.section-lead{position:absolute;left:0;width:1200px;text-align:center;font-size:14px;line-height:23px}
.service{position:absolute;width:275px;height:275px;border-radius:50%;overflow:hidden;background:linear-gradient(135deg,#e9ddd4,#b58a6e)}
.service .cap{position:absolute;left:0;right:0;bottom:0;height:90px;background:var(--red);border-radius:60% 40% 0 0/45% 35% 0 0;color:var(--white);font-family:'Poppins',sans-serif;font-weight:600;font-size:21px;text-align:center;padding-top:28px}

/* about */
.about-text{left:680px;top:1894px;width:378px;font-size:13.5px;line-height:25.6px;text-align:justify;color:#555}
.about-text p+p{margin-top:25px}

/* fees */
.fee-row{position:absolute;left:152px;width:363px;height:2px;background:var(--pink)}
.fee-name{position:absolute;left:154px;font-family:'Poppins',sans-serif;font-size:17px;color:#444;white-space:nowrap}
.fee-price{position:absolute;left:461px;width:57px;height:57px;border-radius:50%;border:2px solid var(--red);background:var(--white);color:var(--red);font-family:'Poppins',sans-serif;font-weight:600;font-size:15px;display:flex;align-items:center;justify-content:center}
.fee-photo{position:absolute;left:636px;top:2598px;width:376px;height:376px;border-radius:50%;background:linear-gradient(160deg,#eef1f5,#c7ccd6)}

/* footer */
.footer{position:absolute;left:0;top:3200px;width:1200px;height:429px;background:var(--black)}
.f-logo{left:173px;top:3232px;width:200px;display:flex;flex-direction:column;align-items:center;z-index:2}
.f-logo .logo-dot{width:90px;height:90px;margin-bottom:14px}
.f-logo .logo-name{color:var(--white);font-size:20px;line-height:1.2}
.socials{left:170px;top:3401px;display:flex;gap:7px}
.socials i{width:36px;height:36px;border-radius:50%;border:2px solid var(--white)}
.badge{left:186px;top:3460px;width:160px;height:40px;border-radius:6px;background:#6abf3a}
.f-head{font-family:'Poppins',sans-serif;font-weight:600;font-size:21px;color:var(--white);white-space:nowrap;z-index:2}
.contact-item{position:absolute;left:479px;color:var(--white);white-space:nowrap}
.contact-item svg{position:absolute;left:0;top:2px}
.contact-item h4{margin-left:39px;font-family:'Poppins',sans-serif;font-weight:600;font-size:17px;line-height:22px}
.contact-item p{margin-left:39px;font-size:15px;line-height:22px;color:#ddd}
.hours{left:783px;top:3288px;width:320px;font-family:'Poppins',sans-serif;font-size:15px;color:var(--white)}
.hours li{list-style:none;display:flex;height:30px;align-items:center;white-space:nowrap}
.hours .d{width:88px;flex:none}
.hours .l{flex:1;border-bottom:1px dotted #888;margin:4px 16px 0 0;height:1px}
.hours .t{width:96px;flex:none}
.f-line{left:113px;top:3553px;width:974px;height:1px;background:#333}
.copy{left:0;top:3580px;width:1200px;text-align:center;font-size:15px;color:var(--white)}
</style>
</head>
<body>

<div class="hero-photo" role="img" aria-label="Autumn leaves in warm orange and gold"></div>

<div class="abs" style="left:0;top:1683px;width:1200px;height:662px;background:linear-gradient(180deg,#e2f3fb,#cfe1ea 60%,#dfe6e7)" role="img" aria-label="Woman in sportswear kneeling on a beach path holding her knee"></div>

<div class="footer"></div>

<svg class="waves" viewBox="0 0 1200 3629" aria-hidden="true">
  <path d="M0 800 C120 730 240 690 330 700 C520 720 700 850 950 845 C1060 843 1150 810 1200 780 L1200 900 L0 900 Z" fill="#fff"/>
  <path d="M30 795 C120 740 200 715 290 718 C480 730 650 865 890 882 C940 885 970 878 985 868 C930 874 880 870 830 860 C620 820 470 710 290 705 C190 703 110 740 30 795 Z" fill="var(--red)"/>
  <path d="M0 1790 C250 1700 480 1670 720 1690 C900 1705 1060 1755 1200 1800 L1200 1670 L0 1670 Z" fill="#fff"/>
  <path d="M150 1720 C330 1675 520 1676 680 1686 C880 1700 1060 1745 1200 1790 L1200 1780 C1060 1735 880 1692 680 1680 C500 1670 320 1682 150 1720 Z" fill="var(--red)"/>
  <path d="M0 2230 C200 2330 450 2330 640 2320 C880 2305 1060 2260 1200 2210 L1200 2360 L0 2360 Z" fill="#fff"/>
  <path d="M0 2218 C160 2320 420 2345 620 2340 C860 2334 1040 2280 1200 2215 L1200 2230 C1040 2290 860 2330 620 2335 C420 2340 180 2320 0 2235 Z" fill="var(--red)"/>
  <circle cx="824" cy="2786" r="211" fill="none" stroke="var(--coral)" stroke-width="12" stroke-dasharray="1000 330" transform="rotate(150 824 2786)"/>
  <path d="M0 3120 C120 3085 220 3062 340 3064 C540 3068 760 3190 957 3190 C1060 3190 1140 3140 1200 3098 L1200 3210 L0 3210 Z" fill="var(--black)"/>
  <path d="M210 3035 C320 3010 430 3030 560 3085 C700 3145 820 3180 930 3180 C1020 3180 1100 3150 1160 3110 C1090 3168 1010 3196 930 3196 C800 3196 690 3150 550 3095 C420 3045 320 3025 210 3035 Z" fill="var(--red)"/>
</svg>

<header>
  <div class="logo-tab">
    <div class="logo-dot"></div>
    <div class="logo-name">CEDARLINE<br>MASSAGE</div>
  </div>
  <div class="topbar">
    <span><svg width="11" height="14" viewBox="0 0 11 14"><path d="M5.5 0A5.5 5.5 0 0 0 0 5.5C0 9.5 5.5 14 5.5 14S11 9.5 11 5.5A5.5 5.5 0 0 0 5.5 0Zm0 7.5a2 2 0 1 1 0-4 2 2 0 0 1 0 4Z" fill="#fff"/></svg>Lena Hart 24 Harbour Lane Seaford VIC 3198</span>
    <span><svg width="14" height="11" viewBox="0 0 14 11"><rect width="14" height="11" rx="1" fill="#fff"/><path d="M1 1l6 5 6-5" stroke="#c98a3a" fill="none"/></svg>lena@cedarlinemassage.com.au</span>
  </div>
  <nav class="nav">
    <a style="left:57px">Home</a>
    <a style="left:153px">Remedial Massage</a>
    <a style="left:348px">About Me</a>
    <a style="left:471px">Fees</a>
    <a style="left:555px">Contact</a>
    <span class="btn login">Login</span>
  </nav>
</header>

<section class="hero">
  <h1 class="abs hero-title">CEDARLINE MASSAGE</h1>
  <p class="abs hero-sub">SED UT PERSPICIATIS UNDE OMNIS ISTE NATUS ERROR<br>SIT VOLUPTATEM ACCUSANTIUM DOLOREM</p>
  <span class="btn" style="left:592px;top:592px;width:163px;height:53px;font-size:16px">GET STARTED</span>
  <div class="abs dots"><i></i><i class="on"></i><i></i></div>
</section>

<section class="services">
  <h2 class="heading section-title" style="top:905px">Remedial Massage</h2>
  <div class="rule" style="left:575px;top:961px"></div>
  <p class="section-lead" style="top:981px">Sed ut perspiciatis unde omnis iste natus error sit voluptatem accusantium doloremque laudantium</p>
  <div class="service" style="left:136px;top:1045px" role="img" aria-label="Therapist massaging a client's shoulders"><div class="cap">Remedial</div></div>
  <div class="service" style="left:463px;top:1045px" role="img" aria-label="Therapist giving a deep tissue back massage"><div class="cap">Deep Tissue</div></div>
  <div class="service" style="left:793px;top:1045px" role="img" aria-label="Therapist applying tape to a client's shoulder"><div class="cap">Relaxation</div></div>
  <div class="service" style="left:292px;top:1332px;background:linear-gradient(135deg,#f6e4dc,#e89a7c)" role="img" aria-label="Pregnant woman holding her belly"><div class="cap">Pregnancy</div></div>
  <div class="service" style="left:622px;top:1332px;background:linear-gradient(135deg,#caa082,#6e4430)" role="img" aria-label="Hands performing lymphatic massage on a leg"><div class="cap">Lymphatic</div></div>
</section>

<section class="about">
  <h2 class="heading abs" style="left:680px;top:1812px;font-size:40px;z-index:2">About Me</h2>
  <div class="rule" style="left:680px;top:1867px;width:56px"></div>
  <div class="abs about-text">
    <p>I completed my training in Toronto, Canada in 1999 where I obtained a Diploma of Remedial Massage through the Northshore College of Massage Therapy.</p>
    <p>Over the years, I have practiced in several different settings including medical centre, chiropractic clinic, spa and currently am a sole trader in my own practice. I have been helping my clients achieve better health through my treatments for several years. I take special interest in women's health.</p>
  </div>
  <span class="btn" style="left:679px;top:2155px;width:160px;height:57px;font-size:18px">Read More</span>
</section>

<section class="fees">
  <h2 class="heading section-title" style="top:2400px">Fee Schedule</h2>
  <div class="rule" style="left:575px;top:2456px"></div>
  <p class="section-lead" style="top:2476px">I am registered with most health funds. Check your level of cover to see if you are<br>able to claim for remedial massage.</p>

  <span class="fee-name" style="top:2619px">30 min Remedial Massage</span><div class="fee-row" style="top:2658px"></div><span class="fee-price" style="top:2602px">$70</span>
  <span class="fee-name" style="top:2692px">45&nbsp; min Remedial Massage</span><div class="fee-row" style="top:2731px"></div><span class="fee-price" style="top:2675px">$90</span>
  <span class="fee-name" style="top:2766px">60 min&nbsp; Remedial Massage</span><div class="fee-row" style="top:2805px"></div><span class="fee-price" style="top:2749px">$110</span>
  <span class="fee-name" style="top:2840px">90 min Remedial Massage</span><div class="fee-row" style="top:2879px"></div><span class="fee-price" style="top:2823px">$160</span>
  <span class="fee-name" style="top:2913px">Manual Lymphatic Drainage</span><div class="fee-row" style="top:2952px"></div><span class="fee-price" style="top:2896px">$140</span>

  <div class="fee-photo" role="img" aria-label="Practitioner examining an older woman's knee"></div>
</section>

<footer>
  <div class="abs f-logo">
    <div class="logo-dot"></div>
    <div class="logo-name">CEDARLINE<br><span style="font-size:14px">MASSAGE</span></div>
  </div>
  <div class="abs socials"><i></i><i></i><i></i><i></i><i></i></div>
  <div class="abs badge"></div>

  <h3 class="abs f-head" style="left:479px;top:3243px">CONTACT US</h3>
  <div class="contact-item" style="top:3297px">
    <svg width="18" height="22" viewBox="0 0 18 22"><path d="M9 1a7 7 0 0 0-7 7c0 5.5 7 13 7 13s7-7.5 7-13a7 7 0 0 0-7-7Z" fill="none" stroke="#fff" stroke-width="1.5"/><circle cx="9" cy="8" r="2.6" fill="none" stroke="#fff" stroke-width="1.5"/></svg>
    <h4>ADDRESS</h4><p>24 Harbour Lane<br>Seaford VIC 3198</p>
  </div>
  <div class="contact-item" style="top:3387px">
    <svg width="20" height="20" viewBox="0 0 20 20"><path d="M4 1.5l3 3.5-1.8 2.3a12 12 0 0 0 7.5 7.5L15 13l3.5 3-2 2.5C8 18.5 1.5 12 1.5 3.5Z" fill="none" stroke="#fff" stroke-width="1.5" stroke-linejoin="round"/></svg>
    <h4>PHONE</h4><p>0400 555 218</p>
  </div>
  <div class="contact-item" style="top:3454px">
    <svg width="21" height="16" viewBox="0 0 21 16"><rect x="1" y="1" width="19" height="14" fill="none" stroke="#fff" stroke-width="1.5"/><path d="M1 1l9.5 8L20 1" fill="none" stroke="#fff" stroke-width="1.5"/></svg>
    <h4>EMAIL</h4><p>lena@cedarlinemassage.com.au</p>
  </div>

  <h3 class="abs f-head" style="left:783px;top:3240px">OPENING HOURS</h3>
  <ul class="abs hours">
    <li><span class="d">Monday</span><span class="l"></span><span class="t">9:00 - 10:00</span></li>
    <li><span class="d">Tuesday</span><span class="l"></span><span class="t">9:00 - 10:00</span></li>
    <li><span class="d">Wednesday</span><span class="l"></span><span class="t">9:00 - 10:00</span></li>
    <li><span class="d">Thursday</span><span class="l"></span><span class="t">9:00 - 10:00</span></li>
    <li><span class="d">Friday</span><span class="l"></span><span class="t">9:00 - 10:00</span></li>
    <li><span class="d">Saturday</span><span class="l"></span><span class="t">9:00 - 10:00</span></li>
    <li><span class="d">Sunday</span><span class="l"></span><span class="t">Closed</span></li>
  </ul>
  <div class="abs f-line"></div>
  <p class="abs copy">©2022 Cedarline Massage.All rights reserved.</p>
</footer>

</body>
</html>
```